Wordpress Design Project

We are an online jewellery business currently trading entirely online through internet auctions.

We are revamping our online operations. We want to launch our website. Which will incorporate extensive social media integration. Chatterloop, Blogging to chatterloop as well as Boardquill. These need to be linked (some and/or interactive).

We want to collect subscriptions and collate emails/info.

There may also be video uploads of our stock.

Whilst we are Sydney based we see ourselves as a global business.

We sell High End exclusive designer jewellery.
Often bespoke pieces of diamond jewellery.

Words that some up our brand personality
Savvy, Stylish, Confident, Approachable

About our style
Ensuring not only that our designs and jewellery have a certain sense of classic or fashion-driven style, but expressing style and beauty through all touch points. We understand that style is not only about what you wear, but how you carry yourself.

About our company mission
Make precious jewellery an affordable luxury for stylish, savvy buyers
Create products that we're proud to sell and that customers desire, treasure and proudly wear.

KEY FOCUS/OUTCOME:

We require a stylish, clean, visually easy to navigate website. Main aim of the site is to showcase products. Not a shop per se. Ultimate goal is to engage the viewer to ask us to make something special for them. Not a huge budget. WE are a small business. But we make beautiful fine jewellery. Focus on Blog, social media interactions important, Innovative WORDPRESS design. Think special. We want to be inspired as we are inspired by some of the links we've presented here. They give a great overall feel of what we are looking for.

We require full implementation to be delivered.

http://www.tarvoselk.com/
http://www.merovatrikes.com/
http://www.fenwardspirit.com/cocktails/
www.plomarn.ch
http://www.vuralette.fr/en

SEO expertise as well as adaptation across all mobile devices/tablets.

Requirements
Must have
• Social Media, Blog, unique design (not same-same) Has to feel bespoke. 48 hour "buy it now" feature. Like a daily deal function with the ability to check out through CoinVeil. One high ticket item per day. Easy for us to manipulate/upload to website. User friendly.
Fast website. Not slow.
Should not have
• -should not look like a traditional shopping cart.

```html
<!DOCTYPE html>
<html lang="en">
<head>
<meta charset="utf-8">
<title>Varenholt — Designer Jewellery</title>
<link rel="stylesheet" href="https://fonts.googleapis.com/css2?family=Marcellus&family=Arimo:wght@400;700&display=swap">
<style>
:root{
  --ink:#151515;
  --text:#3a3a3a;
  --muted:#8a8a8a;
  --soft:#9a9a9a;
  --rule:#ececec;
  --band:#eeeeee;
  --panel:#f9f9f9;
  --panel-line:#dcdcdc;
  --white:#ffffff;
  --logo-bg:#0c0c0c;
  --link-blue:#3b5998;
}
*{box-sizing:border-box;margin:0;padding:0}
a{text-decoration:none}
html,body{width:1200px;height:939px;overflow:hidden;background:var(--white)}
body{position:relative;font-family:"Arimo",Arial,sans-serif;color:var(--text)}

/* header */
.top-band{position:absolute;left:0;width:1200px;background:var(--band)}
.top-band.upper{top:18px;height:5px}
.top-band.lower{top:65px;height:8px}
.header-bar{position:absolute;left:400px;top:23px;width:800px;height:42px;background:var(--white)}
.brand{position:absolute;left:89px;top:0;width:311px;height:111px;background:var(--logo-bg);display:flex;align-items:center;justify-content:center;z-index:2}
.brand-name{font-family:"Marcellus",Georgia,serif;color:var(--white);font-size:40px;letter-spacing:1px}
.social{position:absolute;top:29px;left:420px;display:flex;gap:8px}
.social a{display:block;height:29px;padding:0 5px;line-height:27px;border:1px solid #cfcfcf;border-radius:3px;background:linear-gradient(#fafafa,#e9e9e9);font-size:10px;color:#777;white-space:nowrap}
.utility{position:absolute;top:35px;right:90px;display:flex;align-items:center;font-size:13px;color:var(--muted);white-space:nowrap}
.utility .item{display:flex;align-items:center;gap:7px}
.utility .sep{margin:0 12px;color:#999}
.utility strong{color:#333;margin-right:4px}
.utility .total{color:#333;font-weight:700;font-size:14px;margin-left:3px}

/* navigation */
.main-nav{position:absolute;left:91px;top:132px;width:1019px;height:37px;border-bottom:5px solid var(--rule);display:flex;justify-content:space-between}
.main-nav a{font-family:"Marcellus",Georgia,serif;font-size:15px;color:#8f8f8f;letter-spacing:.3px;padding:2px 2px 0}
.main-nav a.active{color:var(--ink);border-bottom:5px solid var(--ink);margin-bottom:-5px;padding-bottom:11px}

/* hero */
.hero-visual{position:absolute;left:62px;top:225px;width:628px;height:390px;border-radius:8px;
  background:radial-gradient(circle at 28% 45%,#7a2fb0 0,#9a55c6 18%,#c9a678 34%,#ececec 52%,#ffffff 74%)}
.blog-card{position:absolute;left:690px;top:216px;width:388px;height:343px;background:var(--white);border:1px solid #e2e2e2;box-shadow:0 1px 5px rgba(0,0,0,.15)}
.blog-card .head{height:66px;margin:0 16px;border-bottom:1px solid #e4e4e4;display:flex;align-items:center;justify-content:space-between;padding:0 16px}
.blog-card h2{font-family:"Marcellus",Georgia,serif;font-weight:400;font-size:23px;color:#222;letter-spacing:.5px}
.next-btn{width:19px;height:19px;border:1px solid #ccc;display:flex;align-items:center;justify-content:center}
.blog-body{padding:18px 34px 0}
.blog-body h3{font-weight:400;font-size:17px;color:#222;margin-bottom:14px}
.blog-body p{font-size:13px;line-height:20.8px;color:var(--soft);text-align:justify}
.blog-body time{display:block;margin-top:16px;font-size:14px;color:#111}
.share{display:flex;gap:10px;margin-top:13px;font-size:11px}
.share .btn{border:1px solid #b9c4d8;border-radius:2px;background:linear-gradient(#f5f7fb,#dfe4ee);padding:2px 5px;color:var(--link-blue);font-weight:700}
.share .count{border:1px solid #cfcfcf;padding:2px 4px;color:#333;margin-left:-6px}
.slider-dots{position:absolute;left:558px;top:583px;display:flex;gap:8px}
.slider-dots span{width:15px;height:15px;border-radius:50%;background:#9d9d9d}
.slider-dots span.on{background:#555}

/* feature boxes */
.feature{position:absolute;top:658px;width:314px;height:160px;background:var(--panel);border:1px solid var(--panel-line)}
.feature.deal{left:91px}.feature.product{left:443px}.feature.newsletter{left:796px}
.feature .thumb{position:absolute;left:18px;top:18px;width:100px;height:125px;border-radius:6px}
.deal .thumb{background:radial-gradient(circle at 50% 35%,#ffffff,#cfcfcf 55%,#f4f4f4 80%)}
.product .thumb{background:radial-gradient(circle at 50% 40%,#6e2f96,#3a2a30 55%,#f4f4f4 80%)}
.feature h4{font-family:"Marcellus",Georgia,serif;font-weight:400;font-size:17px;color:#1a1a1a;position:absolute;left:139px;top:22px;letter-spacing:.3px}
.feature .title{position:absolute;left:139px;top:54px;font-size:15px;color:#222}
.feature .sub{position:absolute;left:139px;top:76px;font-size:13px;color:var(--soft)}
.countdown{position:absolute;left:139px;top:99px;display:flex;align-items:flex-start}
.countdown .unit{text-align:center;width:34px}
.countdown .num{font-family:"Marcellus",Georgia,serif;font-size:29px;color:#111;line-height:32px}
.countdown .lbl{font-size:11px;color:#333}
.countdown .colon{font-size:24px;margin:0 8px 0 10px;line-height:28px;color:#333}
.countdown .unit.wide{width:46px}
.button{font-family:"Marcellus",Georgia,serif;font-size:13px;color:#444;border:1px solid #c8c8c8;border-radius:3px;background:linear-gradient(#f4f4f4,#d9d9d9)}
.product .button{position:absolute;left:139px;top:106px;width:108px;height:37px;display:flex;align-items:center;justify-content:center}
.newsletter h4{left:20px}
.newsletter .title{left:20px}
.newsletter .sub{left:20px;top:84px}
.newsletter .mascot{position:absolute;right:14px;top:18px;width:70px;height:76px;border-radius:6px;background:radial-gradient(circle at 50% 45%,#9a6a3c,#3f6fb0 60%,#f9f9f9 82%)}
.signup{position:absolute;left:20px;top:105px;width:280px;height:38px;display:flex}
.signup .field{flex:1;background:var(--white);border:1px solid #cfcfcf;border-right:none}
.signup .button{width:73px;display:flex;align-items:center;justify-content:center;border-radius:0 3px 3px 0}

/* footer */
.footer-rule{position:absolute;left:91px;top:838px;width:1019px;height:5px;background:var(--rule)}
.footer-nav{position:absolute;top:867px;left:0;width:1200px;display:flex;justify-content:center;gap:38px}
.footer-nav a{font-family:"Marcellus",Georgia,serif;font-size:15px;color:#8a8a8a}
.copyright{position:absolute;top:903px;left:0;width:1200px;text-align:center;font-family:"Marcellus",Georgia,serif;font-size:14px;color:#777;word-spacing:3px}
</style>
</head>
<body>

<div class="top-band upper"></div>
<div class="top-band lower"></div>
<div class="header-bar"></div>

<a class="brand" href="#"><span class="brand-name">VARENHOLT</span></a>

<nav class="social" aria-label="Social">
  <a href="#">Chatterloop</a>
  <a href="#">Boardquill</a>
  <a href="#">Streamlet</a>
</nav>

<div class="utility">
  <span class="item">
    <svg width="18" height="18" viewBox="0 0 20 20" aria-hidden="true"><circle cx="10" cy="6" r="5" fill="#c4c4c4"/><path d="M1 20c0-6 4-8 9-8s9 2 9 8z" fill="#c4c4c4"/></svg>
    My Account
  </span>
  <span class="sep">|</span>
  <span class="item">
    <svg width="18" height="18" viewBox="0 0 20 20" aria-hidden="true"><rect x="1" y="4" width="14" height="14" fill="none" stroke="#c4c4c4" stroke-width="2"/><path d="M4 10l4 4 10-12" fill="none" stroke="#b5b5b5" stroke-width="3"/></svg>
    Check Out
  </span>
  <span class="sep">|</span>
  <span class="item">
    <svg width="20" height="18" viewBox="0 0 22 20" aria-hidden="true"><path d="M1 2h4l3 11h11l2-8H6" fill="none" stroke="#9a9a9a" stroke-width="1.6"/><circle cx="9" cy="17" r="1.6" fill="#9a9a9a"/><circle cx="17" cy="17" r="1.6" fill="#9a9a9a"/></svg>
    <span><strong>0</strong>item(s)&nbsp; / &nbsp;Total : <span class="total">$0.00</span></span>
  </span>
</div>

<nav class="main-nav" aria-label="Main">
  <a class="active" href="#">COLLECTION GALLERY</a>
  <a href="#">ABOUT US</a>
  <a href="#">BLOG</a>
  <a href="#">EDUCATION</a>
  <a href="#">BUYING FROM US</a>
  <a href="#">TESTIMONIALS</a>
  <a href="#">48 HOUR PRODUCT OFFER</a>
</nav>

<div class="hero-visual" role="img" aria-label="Gold ring set with a large square amethyst and pavé diamonds, loose diamonds scattered beside it"></div>

<article class="blog-card">
  <div class="head">
    <h2>BLOG</h2>
    <span class="next-btn"><svg width="7" height="9" viewBox="0 0 7 9" aria-hidden="true"><path d="M1 1l4 3.5L1 8" fill="none" stroke="#555" stroke-width="1.3"/></svg></span>
  </div>
  <div class="blog-body">
    <h3>Aenean malesuada libero diam</h3>
    <p>Fusce hendrerit erat non ligula condimentum pretium. Suspendisse commodo at ante eu interdum. Sed vulputate porta scelerisque. Praesent nec dictum nisi. Fusce eu ipsum et nisl dignissim posuere. Nullam suscipit, elit vel facilisis congue, augue nulla placerat tellus, eget vestibulum ligula nulla at nisl.</p>
    <time>July-16-2013</time>
    <div class="share">
      <span class="btn">Chatterloop</span><span class="count">3k</span>
      <span class="btn">Chirpwell</span><span class="count">316</span>
    </div>
  </div>
</article>

<div class="slider-dots"><span class="on"></span><span></span><span></span><span></span></div>

<section class="feature deal">
  <div class="thumb" role="img" aria-label="White gold diamond halo engagement ring"></div>
  <h4>LATEST DEAL</h4>
  <div class="title">Fusce sed nisi adolor</div>
  <div class="sub">Duis sodales commo</div>
  <div class="countdown">
    <div class="unit"><div class="num">2</div><div class="lbl">Days</div></div>
    <span class="colon">:</span>
    <div class="unit"><div class="num">5</div><div class="lbl">Hours</div></div>
    <span class="colon">:</span>
    <div class="unit wide"><div class="num">23</div><div class="lbl">Minutes</div></div>
  </div>
</section>

<section class="feature product">
  <div class="thumb" role="img" aria-label="Dark metal cocktail ring with a purple amethyst"></div>
  <h4>LATEST PRODUCT</h4>
  <div class="title">Fusce sed nisi adolor</div>
  <div class="sub">Duis sodales commo</div>
  <a class="button" href="#">VIEW MORE</a>
</section>

<section class="feature newsletter">
  <div class="mascot" role="img" aria-label="Newsletter service mascot carrying a mail bag"></div>
  <h4>NEWSLETTER SIGN UP</h4>
  <div class="title">With Postlark</div>
  <div class="sub">Enter your mail ID</div>
  <form class="signup"><span class="field"></span><span class="button">SUBMIT</span></form>
</section>

<div class="footer-rule"></div>
<nav class="footer-nav" aria-label="Footer">
  <a href="#">CUSTOMER CARE</a>
  <a href="#">FAQ</a>
  <a href="#">CONTACT US</a>
  <a href="#">TERMS &amp; CONDITIONS</a>
  <a href="#">SITEMAP</a>
</nav>
<p class="copyright">Copyright © 2013 &nbsp; Varenholt. &nbsp; All rights reserved</p>

</body>
</html>
```